KLV Plant Services

We are a heavy diesel mechanical business with additional air con certificates, remapping engine rebuilt

Contact Information for Business Card

Company Name, Director Name, Managing Director, Contact details, email and website

Font styles to use
Serif
Script

```html
<!DOCTYPE html>
<html lang="en">
<head>
<meta charset="utf-8">
<title>KLV Plant Services – Business Card</title>
<link rel="stylesheet" href="https://fonts.googleapis.com/css2?family=Montserrat:ital,wght@0,400;0,700;0,800;1,400&display=swap">
<style>
  :root {
    --navy: #0a0a78;
    --navy-deep: #070763;
    --white: #ffffff;
    --ink: #0b0b0b;
    --page: #e6e6e6;
  }
  * { margin: 0; padding: 0; box-sizing: border-box; }
  html, body {
    width: 1200px; height: 900px; overflow: hidden;
    background: var(--page);
    font-family: "Montserrat", sans-serif;
  }
  .sheet {
    width: 1200px; height: 900px;
    display: flex; flex-direction: column; align-items: center; justify-content: center;
    gap: 40px;
  }
  .card {
    position: relative;
    width: 700px; height: 400px;
    overflow: hidden;
    box-shadow: 0 8px 24px rgba(0,0,0,.25);
  }
  /* Back side */
  .card-back {
    background: var(--navy);
  }
  .card-back .texture {
    position: absolute; inset: 0;
    background: linear-gradient(135deg, var(--navy) 0%, var(--navy-deep) 100%);
  }
  .card-back .corner-name {
    position: absolute; right: 34px; top: 150px;
    color: var(--white);
    font-weight: 800; font-size: 15px; line-height: 1.05;
    text-align: center;
  }
  .card-back .corner-name small { display: block; font-size: 8px; font-weight: 800; }

  /* Front side */
  .card-front { background: var(--navy); }
  .card-front .shape { position: absolute; inset: 0; }
  .contact {
    position: absolute; left: 56px; top: 70px;
    color: var(--white);
  }
  .person-name {
    font-weight: 800; font-size: 27px; letter-spacing: .5px; text-transform: uppercase;
  }
  .person-role { font-style: italic; font-size: 15px; margin-top: 2px; }
  .address { font-size: 17px; line-height: 1.3; margin: 30px 0 0 14px; }
  .lines { list-style: none; margin-top: 26px; font-size: 18px; line-height: 1.32; }
  .lines li { display: flex; align-items: center; gap: 8px; }
  .lines svg { width: 13px; height: 13px; flex: none; }
  .brand {
    position: absolute; left: 470px; top: 150px; width: 210px;
    color: var(--navy);
    font-weight: 800; text-align: center; line-height: 1;
  }
  .brand .brand-main { display: block; font-size: 62px; letter-spacing: 1px; }
  .brand .brand-sub { display: block; font-size: 22px; margin-top: 4px; }
</style>
</head>
<body>
<main class="sheet">
  <section class="card card-back" aria-label="Card back">
    <div class="texture" role="img" aria-label="Tonal navy embossed pattern"></div>
    <div class="corner-name">KLV<small>Plant Services</small></div>
  </section>

  <section class="card card-front" aria-label="Card front">
    <svg class="shape" viewBox="0 0 700 400" aria-hidden="true">
      <path d="M470 0 L700 0 L700 400 L520 400 C360 350 335 70 470 0 Z" fill="var(--white)"/>
      <path d="M486 6 C370 60 362 320 540 398 C398 318 390 86 486 6 Z" fill="var(--ink)"/>
    </svg>

    <div class="contact">
      <h1 class="person-name">Mark Ellison</h1>
      <p class="person-role">Director</p>
      <p class="address">2270 Harlow Ridge Rd Norcross<br>Park, GA 30095</p>
      <ul class="lines">
        <li>
          <svg viewBox="0 0 24 24"><path fill="#fff" d="M6.6 10.8a15 15 0 0 0 6.6 6.6l2.2-2.2c.3-.3.7-.4 1-.2 1.1.4 2.3.6 3.6.6.6 0 1 .4 1 1V20c0 .6-.4 1-1 1A17 17 0 0 1 3 4c0-.6.4-1 1-1h3.5c.6 0 1 .4 1 1 0 1.3.2 2.5.6 3.6.1.3 0 .7-.2 1z"/></svg>
          470-555-0148
        </li>
        <li>
          <svg viewBox="0 0 24 24"><rect x="2" y="5" width="20" height="14" rx="1" fill="none" stroke="#fff" stroke-width="2"/><path d="M2 6l10 7 10-7" fill="none" stroke="#fff" stroke-width="2"/></svg>
          info@klvplantservices.com
        </li>
        <li>
          <svg viewBox="0 0 24 24"><circle cx="12" cy="12" r="10" fill="none" stroke="#fff" stroke-width="2"/><path d="M2 12h20M12 2c3 3 3 17 0 20M12 2c-3 3-3 17 0 20" fill="none" stroke="#fff" stroke-width="2"/></svg>
          www.klvplantservices.com
        </li>
      </ul>
    </div>

    <div class="brand">
      <span class="brand-main">KLV</span>
      <span class="brand-sub">Plant Services</span>
    </div>
  </section>
</main>
</body>
</html>
```